"Vine Hollow Excursions" is a top notch Santa Barbara County Wine Tour company.

We provide scenic, boutique and custom wine tours. I need the card to be clean and classy. I will provide our logo. I would like the logo to cover the back side of the card as an option and would like to see a couple color options other then our signature green and gold. I would like to see some creative options and let the designers come up with options.
I need cards for myself and my team. The final design should communicate "An authentic and boutique wine tour experience"
Please use my website for reference www.vinehollowexcursions.example

Target Market(s)

We have a wide range of clients from millennials to baby boomers

Industry/Entity Type

Tour

Contact Information for Business Card

Contact info:
Dale Morton
805-219-6384
info@vinehollowexcursions.example
vinehollowexcursions.example

Colors

Designer to choose colors to be used in the design.

Requirements
Must have
• my logo
Nice to have
• *I would like to have the backside side with the logo and the company statement
• "An authentic and boutique wine tour experience" as an option.
• *I would also like to see what the designers can create!
• *I would like to see an option that incorporates or social: instagram, yelp, Tour Advisor
Should not have
• I do not want it too busy.

```html
<!DOCTYPE html>
<html lang="en">
<head>
<meta charset="utf-8">
<title>Vine Hollow Excursions — Business Card</title>
<link href="https://fonts.googleapis.com/css2?family=Oswald:wght@500&family=Open+Sans:wght@400;600&display=swap" rel="stylesheet">
<style>
  :root {
    --backdrop: #2b2b2b;
    --card-white: #ffffff;
    --card-black: #1c1c1c;
    --vine-green: #246b43;
    --gold: #b89878;
    --grey-band: #c9c9cb;
    --grey-light: #e4e4e6;
    --ink: #555555;
    --ink-dark: #333333;
  }
  * { margin: 0; padding: 0; box-sizing: border-box; }
  html, body { width: 1200px; height: 900px; overflow: hidden; background: var(--backdrop); }
  .canvas { position: relative; width: 1200px; height: 900px; }
  .card {
    position: absolute; width: 560px; height: 320px; border-radius: 22px; overflow: hidden;
    box-shadow: 0 18px 40px rgba(0,0,0,.45);
  }
  .card--back { left: 580px; top: 110px; background: var(--card-black); }
  .card--front { left: 70px; top: 470px; background: var(--card-white); }

  .brand { display: flex; align-items: center; gap: 10px; }
  .brand__dot { border-radius: 50%; background: var(--vine-green); flex: none; }
  .brand__name { font-family: "Open Sans", sans-serif; font-weight: 600; color: var(--gold); white-space: nowrap; }

  .card--back .brand { position: absolute; left: 0; right: 0; top: 144px; justify-content: center; }
  .card--back .brand__dot { width: 18px; height: 18px; }
  .card--back .brand__name { font-size: 24px; }

  .wave { position: absolute; inset: 0; }
  .card--front .brand { position: absolute; left: 36px; top: 30px; }
  .card--front .brand__dot { width: 14px; height: 14px; }
  .card--front .brand__name { font-size: 16px; }
  .divider { position: absolute; left: 36px; right: 36px; top: 76px; height: 1.5px; background: var(--vine-green); }

  .socials { position: absolute; left: 36px; top: 90px; list-style: none; font-family: "Open Sans", sans-serif; font-size: 12px; color: var(--ink); }
  .socials li { display: flex; align-items: center; gap: 7px; height: 17px; }
  .icon-dot { width: 10px; height: 10px; border-radius: 50%; background: var(--vine-green); flex: none; }

  .person { position: absolute; right: 36px; top: 168px; text-align: right; width: 240px; }
  .person__name { font-family: "Oswald", sans-serif; font-weight: 500; font-size: 28px; color: var(--vine-green); line-height: 1; letter-spacing: .5px; }
  .person__role { font-family: "Open Sans", sans-serif; font-size: 12px; color: var(--gold); letter-spacing: 1px; margin-top: 4px; }
  .person__rule { height: 1.5px; background: var(--vine-green); margin-top: 6px; }

  .contacts { position: absolute; right: 36px; top: 236px; list-style: none; font-family: "Open Sans", sans-serif; font-size: 12px; color: var(--ink); text-align: right; }
  .contacts li { display: flex; justify-content: flex-end; align-items: center; gap: 8px; height: 18px; }
  .contacts .web { font-weight: 600; color: var(--ink-dark); }
</style>
</head>
<body>
<main class="canvas">
  <section class="card card--back" aria-label="Card back">
    <div class="brand"><span class="brand__dot"></span><span class="brand__name">Vine Hollow Excursions</span></div>
  </section>

  <section class="card card--front" aria-label="Card front">
    <svg class="wave" viewBox="0 0 560 320" preserveAspectRatio="none" aria-hidden="true">
      <path d="M0 95 C40 180 160 210 250 250 C300 272 330 300 345 320 L0 320 Z" fill="var(--grey-light)"/>
      <path d="M0 130 C30 200 140 225 220 260 C260 278 285 300 300 320 L0 320 Z" fill="var(--grey-band)"/>
      <path d="M0 175 C30 230 130 250 190 275 C225 290 245 305 255 320 L0 320 Z" fill="var(--vine-green)"/>
    </svg>

    <div class="brand"><span class="brand__dot"></span><span class="brand__name">Vine Hollow Excursions</span></div>
    <div class="divider"></div>

    <ul class="socials">
      <li><span class="icon-dot"></span>/vinehollowexcursions</li>
      <li><span class="icon-dot"></span>@vinehollowexcursions</li>
      <li><span class="icon-dot"></span>/biz/vinehollowexcursions</li>
      <li><span class="icon-dot"></span>@sbcvinetrips</li>
    </ul>

    <div class="person">
      <div class="person__name">DALE MORTON</div>
      <div class="person__role">TOUR ADVISOR</div>
      <div class="person__rule"></div>
    </div>

    <ul class="contacts">
      <li>805-219-6384<span class="icon-dot"></span></li>
      <li>info@vinehollowexcursions.example<span class="icon-dot"></span></li>
      <li class="web">www.vinehollowexcursions.example<span class="icon-dot"></span></li>
    </ul>
  </section>
</main>
</body>
</html>
```